Sale- Bundle signs

We are looking for a design to use for Permanent SALE/Bundle deal signs. We are a natural bath products company who uses all natural ingredients to create our handmade line of natural products. We love a clean, fresh look and feel. Simple eye-catching that will be a quick glance and they will know the offer.
We would like to have something simple, eye catching that will promote sales on our different products.
Dead Sea Salt Body Scrubs
large 2 for $40
small 3 for $20
Moisturizing Wash with coconut & olive oil
2 for $20
There are several more needed but we are hoping to decide on one template before making all of the signs.
Visit our website here www.tamberlinewash.com
Target Market(s)
Our store serves 70% women and the majority of our customers are 30+ years old.
Industry/Entity Type
It Company
Other font styles liked:
- Century Gothic or similar
Look and feel
Each slider illustrates characteristics of the customer's brand and the style your logo design should communicate.

```html
<!DOCTYPE html>
<html lang="en">
<head>
<meta charset="utf-8">
<title>Tamberline Bundle Sign</title>
<link href="https://fonts.googleapis.com/css2?family=Questrial&family=Nunito:wght@800&display=swap" rel="stylesheet">
<style>
  :root {
    --offer-blue: #1c9bd1;
    --ink: #141414;
    --body-ink: #222222;
    --paper: #ffffff;
    --sun-yellow: #f6c21a;
    --sun-orange: #f2a51c;
    --leaf-green: #9cc625;
  }
  html, body {
    margin: 0;
    padding: 0;
    width: 866px;
    height: 1200px;
    overflow: hidden;
    background: var(--paper);
  }
  .sign {
    position: relative;
    width: 866px;
    height: 1200px;
    overflow: hidden;
    font-family: "Questrial", "Century Gothic", sans-serif;
  }
  .backdrop {
    position: absolute;
    inset: 0;
  }
  .brand {
    position: absolute;
    top: 70px;
    left: 0;
    width: 866px;
    text-align: center;
  }
  .brand-name {
    font-family: "Nunito", "Century Gothic", sans-serif;
    font-weight: 800;
    font-size: 100px;
    line-height: 1;
    color: var(--ink);
    letter-spacing: 0;
  }
  .brand-tagline {
    margin-top: 18px;
    font-size: 36px;
    letter-spacing: 2px;
    color: var(--body-ink);
  }
  .product-title {
    position: absolute;
    left: 0;
    width: 906px;
    text-align: center;
    font-size: 34px;
    line-height: 46px;
    color: var(--body-ink);
    margin: 0;
    font-weight: normal;
  }
  .product-title.scrubs { top: 320px; }
  .product-title.wash { top: 734px; width: 890px; }
  .offer {
    position: absolute;
    left: 20px;
    width: 866px;
    text-align: center;
    font-family: "Nunito", "Century Gothic", sans-serif;
    font-weight: 800;
    font-size: 74px;
    line-height: 1;
    color: var(--offer-blue);
    margin: 0;
  }
  .offer .word { color: var(--ink); }
  .offer.large { top: 424px; }
  .offer.small { top: 544px; }
  .offer.wash { top: 856px; left: 26px; }
  .flower {
    position: absolute;
    left: 48px;
    top: 868px;
    width: 230px;
    height: 230px;
    border-radius: 50%;
    background: radial-gradient(circle at 50% 50%, #f3b51f 0%, #f7e27a 22%, #ffffff 48%, #f1f1ee 70%, rgba(255,255,255,0) 72%);
  }
</style>
</head>
<body>
<main class="sign">
  <svg class="backdrop" width="866" height="1200" viewBox="0 0 866 1200" aria-hidden="true">
    <defs>
      <linearGradient id="warm-field" x1="0" y1="0" x2="0.3" y2="1">
        <stop offset="0" stop-color="#fbe07a"/>
        <stop offset="0.35" stop-color="#f2a51c"/>
        <stop offset="0.6" stop-color="#f6c21a"/>
        <stop offset="1" stop-color="#9cc625"/>
      </linearGradient>
      <linearGradient id="right-field" x1="0" y1="0" x2="0" y2="1">
        <stop offset="0" stop-color="#fdf0b8"/>
        <stop offset="0.5" stop-color="#f8c83a"/>
        <stop offset="1" stop-color="#e9c21c"/>
      </linearGradient>
      <linearGradient id="top-fade" x1="0" y1="0" x2="0" y2="1">
        <stop offset="0.6" stop-color="#ffffff" stop-opacity="1"/>
        <stop offset="1" stop-color="#ffffff" stop-opacity="0"/>
      </linearGradient>
    </defs>
    <rect x="0" y="0" width="866" height="1200" fill="url(#warm-field)"/>
    <rect x="600" y="500" width="266" height="700" fill="url(#right-field)"/>
    <rect x="0" y="0" width="866" height="190" fill="url(#top-fade)"/>
    <circle cx="500" cy="395" r="410" fill="#ffffff"/>
    <circle cx="555" cy="885" r="355" fill="#ffffff"/>
    <circle cx="135" cy="665" r="40" fill="#ffffff" opacity="0.25"/>
    <circle cx="145" cy="725" r="55" fill="#ffffff" opacity="0.2"/>
    <circle cx="790" cy="1060" r="60" fill="#ffffff" opacity="0.25"/>
  </svg>

  <header class="brand">
    <div class="brand-name">tamberline</div>
    <div class="brand-tagline">NATURAL BATH PRODUCTS</div>
  </header>

  <h2 class="product-title scrubs">DEAD SEA SALT<br>BODY SCRUBS</h2>
  <p class="offer large">Large 2 <span class="word">for</span> $40</p>
  <p class="offer small">Small 3 <span class="word">for</span> $20</p>

  <h2 class="product-title wash">MOISTURIZING WASH WITH<br>COCONUT &amp; OLIVE OIL</h2>
  <p class="offer wash">2 <span class="word">for</span> $20</p>

  <div class="flower" role="img" aria-label="White frangipani flower with a yellow centre and water droplets"></div>
</main>
</body>
</html>
```